Homemaking training schools needs a Business Card design

Designer, Hello!

No special requirements, good-looking enough.
--------------------------------------------------------------------------

Name: Marcus Dole
Chairman
Tel: 0574-71948263
Mobile: 13857420916
Email: kelvora@mailnest.example
Web: www.prt2019.example
Add: No.258, LanpingJie, BeiyuanQu, Ningbo, Zhejiang

LOGO
Ningbo PRT Homemaking Training School

Target Market(s)

pregnant women, mothers, infants, the elderly and families, including cleaning, cooking, nursing training.

Industry/Entity Type

Business

Contact Information for Business Card

Name: Marcus Dole
Chairman
Tel: 0574-71948263
Mobile: 13857420916
Email: kelvora@mailnest.example
Web: www.prt2019.example

LOGO

Font styles to use
Serif
Sans Serif
Decorative

Requirements
Nice to have
• Feels: clean, specifications, safety, comfort, warmth and happiness.

```html
<!DOCTYPE html>
<html lang="en">
<head>
<meta charset="utf-8">
<title>PeiRanTang Business Card</title>
<link rel="stylesheet" href="https://fonts.googleapis.com/css2?family=Quicksand:wght@400;500;700&display=swap">
<style>
  :root {
    --backdrop: #e6e6e6;
    --card-light: #f7f7f7;
    --card-dark: #1c1c1e;
    --brand-blue: #1f76bd;
    --brand-pink: #e2168c;
    --ink: #4a4a4a;
    --ink-soft: #8a8a8a;
    --ink-dark-card: #6b6b6b;
    --white: #ffffff;
  }
  * { box-sizing: border-box; margin: 0; padding: 0; }
  html, body {
    width: 1200px; height: 801px; overflow: hidden;
    background: var(--backdrop);
    font-family: "Quicksand", sans-serif;
  }
  .stage {
    position: relative; width: 1200px; height: 801px;
    display: flex; justify-content: center; align-items: center; gap: 70px;
  }
  .card {
    position: relative; width: 330px; height: 550px; overflow: hidden;
    box-shadow: 0 14px 30px rgba(0,0,0,0.18);
  }
  .card--light { background: var(--card-light); color: var(--ink); }
  .card--dark { background: var(--card-dark); color: var(--ink-dark-card); }

  .brand { position: absolute; top: 120px; right: 34px; text-align: right; }
  .brand__name {
    font-weight: 700; font-size: 38px; letter-spacing: -0.5px;
    color: var(--brand-blue); line-height: 1;
  }
  .brand__rule {
    height: 2px; width: 250px; margin: 8px 0 6px auto;
    background: var(--ink-soft);
  }
  .brand__tagline { font-size: 13px; color: var(--ink-soft); font-weight: 500; }

  .person { position: absolute; top: 240px; right: 34px; text-align: right; }
  .person__name { font-weight: 700; font-size: 22px; color: var(--brand-blue); }
  .person__name .surname { color: var(--brand-pink); }
  .person__role { font-size: 13px; margin-top: 2px; }

  .contacts {
    position: absolute; top: 330px; left: 22px; right: 22px;
    display: grid; grid-template-columns: auto auto 1fr; column-gap: 6px; row-gap: 7px;
    align-items: center; font-size: 11.5px; font-weight: 500;
  }
  .contacts__labels { display: flex; gap: 2px; }
  .contacts__label {
    font-size: 9px; font-weight: 700; padding: 0 2px;
    border-left: 1.5px solid var(--brand-pink); border-right: 1.5px solid var(--brand-pink);
    color: var(--brand-blue);
  }

  .footer { position: absolute; left: 0; bottom: 0; width: 330px; height: 130px; }
  .footer svg { position: absolute; inset: 0; }
  .footer__address {
    position: absolute; left: 0; right: 0; bottom: 30px;
    text-align: center; color: var(--white); font-size: 13px; font-weight: 500; line-height: 1.5;
  }
</style>
</head>
<body>
<main class="stage">

  <article class="card card--dark">
    <header class="brand">
      <div class="brand__name">PeiRanTang</div>
      <div class="brand__rule"></div>
      <div class="brand__tagline">Training &amp; Services</div>
    </header>
    <section class="person">
      <div class="person__name">Marcus <span class="surname">Dole</span></div>
      <div class="person__role">Chairman</div>
    </section>
    <section class="contacts">
      <span>0574-71948263</span>
      <span class="contacts__labels"><span class="contacts__label">T</span><span class="contacts__label">E</span></span>
      <span>kelvora@mailnest.example</span>
      <span>13857420916</span>
      <span class="contacts__labels"><span class="contacts__label">M</span><span class="contacts__label">W</span></span>
      <span>www.prt2019.example</span>
    </section>
    <footer class="footer">
      <svg width="330" height="130" viewBox="0 0 330 130">
        <path d="M0,40 Q165,-20 330,40 L330,130 L0,130 Z" fill="var(--brand-blue)"/>
        <path d="M0,40 Q165,-20 330,40" fill="none" stroke="var(--brand-pink)" stroke-width="3"/>
      </svg>
      <div class="footer__address">No.258, LanpingJie<br>BeiyuanQu, Ningbo, Zhejiang</div>
    </footer>
  </article>

  <article class="card card--light">
    <header class="brand">
      <div class="brand__name">PeiRanTang</div>
      <div class="brand__rule"></div>
      <div class="brand__tagline">Training &amp; Services</div>
    </header>
    <section class="person">
      <div class="person__name">Marcus <span class="surname">Dole</span></div>
      <div class="person__role">Chairman</div>
    </section>
    <section class="contacts">
      <span>0574-71948263</span>
      <span class="contacts__labels"><span class="contacts__label">T</span><span class="contacts__label">E</span></span>
      <span>kelvora@mailnest.example</span>
      <span>13857420916</span>
      <span class="contacts__labels"><span class="contacts__label">M</span><span class="contacts__label">W</span></span>
      <span>www.prt2019.example</span>
    </section>
    <footer class="footer">
      <svg width="330" height="130" viewBox="0 0 330 130">
        <path d="M0,40 Q165,-20 330,40 L330,130 L0,130 Z" fill="var(--brand-blue)"/>
        <path d="M0,40 Q165,-20 330,40" fill="none" stroke="var(--brand-pink)" stroke-width="3"/>
      </svg>
      <div class="footer__address">No.258, LanpingJie<br>BeiyuanQu, Ningbo, Zhejiang</div>
    </footer>
  </article>

</main>
</body>
</html>
```